Business Card Design Project

Business card based on attached logo

Todd Merrick
Todd@lorvantest.com
877-514-9073 ext. 318
Www.LorvanTest.com

Industry/Entity Type

Business

```html
<!DOCTYPE html>
<html lang="en">
<head>
<meta charset="utf-8">
<title>LorvanTest Business Cards</title>
<link rel="stylesheet" href="https://fonts.googleapis.com/css2?family=Arimo:wght@400;700&display=swap">
<style>
  :root {
    --board: #8a8c8f;
    --paper: #ffffff;
    --ink: #231f20;
    --brand-red: #e3262b;
    --red-deep: #c8202a;
    --charcoal: #252525;
    --charcoal-light: #3a3a3a;
    --white: #ffffff;
  }
  * { margin: 0; padding: 0; box-sizing: border-box; }
  html, body {
    width: 1200px;
    height: 720px;
    overflow: hidden;
    background: var(--board);
    font-family: "Arimo", Arial, sans-serif;
  }
  .sheet { position: relative; width: 1200px; height: 720px; }
  .card {
    position: absolute;
    width: 564px;
    height: 322px;
    overflow: hidden;
  }
  .card--contact { left: 26px; top: 26px; background: var(--paper); }
  .card--red { left: 612px; top: 26px; background: linear-gradient(135deg, var(--brand-red) 0%, var(--red-deep) 100%); }
  .card--white { left: 26px; top: 373px; background: var(--paper); }
  .card--dark { left: 612px; top: 373px; background: radial-gradient(ellipse at 50% 35%, var(--charcoal-light) 0%, var(--charcoal) 70%); }

  .brand {
    position: absolute;
    display: flex;
    align-items: flex-start;
    gap: 8px;
    font-weight: 700;
    letter-spacing: -1px;
    line-height: 1;
  }
  .brand__mark { width: 18px; height: 18px; background: var(--brand-red); flex: none; }
  .brand--small { top: 62px; left: 0; right: 0; justify-content: center; font-size: 58px; color: var(--ink); }
  .brand--large { top: 104px; left: 0; right: 0; justify-content: center; font-size: 78px; color: var(--ink); }
  .brand--large .brand__mark { width: 24px; height: 24px; }
  .brand--on-red { top: 52px; left: 36px; font-size: 92px; color: var(--white); }
  .brand--on-dark { top: 104px; left: 0; right: 0; justify-content: center; font-size: 78px; color: var(--white); }
  .brand--on-dark .brand__mark { width: 24px; height: 24px; background: var(--white); }

  .holder {
    position: absolute;
    top: 198px; left: 0; right: 0;
    text-align: center;
    color: var(--brand-red);
    font-size: 18px;
    letter-spacing: 0.5px;
  }
  .rule-red { position: absolute; left: 0; right: 0; top: 226px; height: 3px; background: var(--brand-red); }
  .contact-band {
    position: absolute; left: 0; right: 0; top: 232px; bottom: 0;
    background: var(--charcoal);
    color: var(--white);
    font-size: 16px;
  }
  .contact-line {
    position: absolute; left: 0; right: 0;
    display: flex; justify-content: center; align-items: center; gap: 16px;
  }
  .contact-line--phone { top: 21px; }
  .contact-line--web { top: 51px; }
  .contact-item { display: flex; align-items: center; gap: 6px; }
  .contact-item svg { width: 12px; height: 12px; fill: var(--white); }

  .web {
    position: absolute; left: 0; right: 0; bottom: 26px;
    text-align: center;
    font-size: 16px;
    letter-spacing: 3px;
  }
  .card--white .web { color: var(--ink); }
  .card--dark .web { color: var(--white); }
  .card--red .web { left: 36px; right: auto; bottom: 16px; color: var(--white); }

  .decor-square {
    position: absolute;
    right: -20px; bottom: 56px;
    width: 140px; height: 140px;
    background: rgba(255, 255, 255, 0.12);
  }
</style>
</head>
<body>
<main class="sheet">

  <section class="card card--contact">
    <div class="brand brand--small"><span>LorvanTest</span><span class="brand__mark"></span></div>
    <p class="holder">TODD MERRICK</p>
    <div class="rule-red"></div>
    <div class="contact-band">
      <div class="contact-line contact-line--phone">
        <span class="contact-item">
          <svg viewBox="0 0 12 12" aria-hidden="true"><path d="M2.5 0.8l2 2-1 1.3c.6 1.5 1.9 2.8 3.4 3.4l1.3-1 2 2-1.2 1.9C5 10.4 1.6 7 0.6 2z"/></svg>
          877-514-9073 ext. 318
        </span>
      </div>
      <div class="contact-line contact-line--web">
        <span class="contact-item">
          <svg viewBox="0 0 12 12" aria-hidden="true"><path d="M0 3h12v8H0z M0 3l6 4 6-4" fill="none" stroke="#fff" stroke-width="1.4"/></svg>
          Todd@lorvantest.com
        </span>
        <span class="contact-item">
          <svg viewBox="0 0 12 12" aria-hidden="true"><g fill="none" stroke="#fff" stroke-width="1.1"><circle cx="6" cy="6" r="5.2"/><ellipse cx="6" cy="6" rx="2.2" ry="5.2"/><path d="M0.8 6h10.4"/></g></svg>
          www.lorvantest.com
        </span>
      </div>
    </div>
  </section>

  <section class="card card--red">
    <div class="brand brand--on-red"><span>LorvanTest</span></div>
    <div class="decor-square"></div>
    <p class="web">www.lorvantest.com</p>
  </section>

  <section class="card card--white">
    <div class="brand brand--large"><span>LorvanTest</span><span class="brand__mark"></span></div>
    <p class="web">www.lorvantest.com</p>
  </section>

  <section class="card card--dark">
    <div class="brand brand--on-dark"><span>LorvanTest</span><span class="brand__mark"></span></div>
    <p class="web">www.lorvantest.com</p>
  </section>

</main>
</body>
</html>
```